Larkmoor Drones Business Card

We are a new company based in Central Queensland, Australia that uses specalised drones (Voskel Ferra Q80) to undertake mainly agricultural operations, like spraying weeds, spraying crops, spreading seed etc. I have attached a Plimbo proof of a card I was thinking along the lines of - purely a start point. The drone used in the business card MUST be a Voskel Ferra Q80.
I am very open to other ideas, especially fonts and layout. I don't have website etc set up yet.
The images are stock and easily interchangeable, I just ask that any background images reflect the local central Queensland area. The photo of the drone is not even complete (propellers cut off) and I need a new stock photo – I’m not sure if this is an issue, or I can pay for an image if need be. PLEASE FIND AN FERRA Q80 image - 4 sprayers, not 6.
The logo/business name is very draft and looking for further ideas, ideally incorporating drones or agriculture design elements into the design of the business name. The business name needs work on the graphic/design – it is a draft that I have included, the drone propellers (being a different colour) are DRAFT only and intended for changes. PLEASE DO NOT USE THE DRONE PORPELLER I HAVE USED AS A DRAFT. TRY TO FIND SOMETHING ELSE.. The arrow is a shape and not aligned in any way, I would also like ideas on different fonts and additional elements, like air streams, aviation elements, aviation or country western (farming like) themes and fonts etc.
Ideally looking at staying within the blue, green and yellow colours, keeping with an natural, outdoorsy, environmental feel.

Target Market(s)

Farmers, Agriculture, Local Governments, Land Managers

Industry/Entity Type

Agriculture, Drones, Aviation

Contact Information for Business Card

Agricultural Drone (Voskel Ferra Q80), Farming, Business Name.

Font styles to use
Sans Serif

Colors
0054AA
0677BA
7BADD7
CADEEF
E8F1F8
0094D4
00A9DD
6FCCEA
C7EBF8
E9F6FB
00AB8E
00BBA5
67D7C9
C6EFE9
E9F9F6
59FF00
82FF00
B8FF75
E3FFCB
F4FFEA

Requirements
Must have
• Voskel Ferra Q80 Drone
Should not have
• Tractors

```html
<!DOCTYPE html>
<html lang="en">
<head>
<meta charset="utf-8">
<title>Larkmoor Drones – Business Card</title>
<link rel="stylesheet" href="https://fonts.googleapis.com/css2?family=Poppins:wght@400;500;700;800&family=Noto+Serif:wght@400&display=swap">
<style>
  :root {
    --backdrop: #b4b4b4;
    --logo-green: #3d6b0c;
    --band-teal: #4aa3c0;
    --sky-top: #bcd8ee;
    --sky-low: #dfeaf2;
    --field-dark: #4f6f1f;
    --field-mid: #6d8a33;
    --field-light: #86a34a;
    --wave-pale: #a9bf8c;
    --drone-white: #f4f5f6;
    --drone-grey: #c9ced3;
    --white: #ffffff;
  }
  * { box-sizing: border-box; margin: 0; padding: 0; }
  html, body { width: 1200px; height: 1015px; overflow: hidden; }
  body { background: var(--backdrop); position: relative; font-family: "Poppins", sans-serif; }

  .card { position: absolute; width: 700px; height: 400px; overflow: hidden; box-shadow: 0 6px 18px rgba(0,0,0,.25); }
  .card--front { left: 90px; top: 70px; }
  .card--back { left: 410px; top: 545px; background: var(--white); }

  .wordmark { position: absolute; color: var(--logo-green); font-family: "Poppins", sans-serif; font-weight: 800; font-size: 60px; line-height: 1; letter-spacing: 1px; text-transform: uppercase; }
  .wordmark span { display: block; }
  .wordmark .line-two { padding-left: 95px; margin-top: 4px; }

  /* front */
  .front-scene { position: absolute; inset: 0; background: linear-gradient(180deg, var(--sky-top) 0%, var(--sky-low) 50%, #7e9a4a 56%, var(--field-mid) 72%, var(--field-dark) 100%); }
  .drone-photo { position: absolute; left: 445px; top: 28px; width: 215px; height: 178px; border-radius: 18px; background: radial-gradient(ellipse at 50% 45%, var(--drone-white) 0%, var(--drone-grey) 55%, rgba(201,206,211,0) 78%); }
  .card--front .wordmark { left: 42px; top: 62px; }
  .region-band { position: absolute; left: 0; right: 0; top: 214px; height: 46px; background: var(--band-teal); color: var(--white); font-weight: 700; font-size: 25px; letter-spacing: .5px; line-height: 46px; padding-left: 38px; text-transform: uppercase; }
  .services { position: absolute; left: 330px; top: 272px; list-style: none; color: var(--white); font-family: "Noto Serif", serif; font-size: 25px; line-height: 37px; }
  .services li:nth-child(2) { padding-left: 22px; }
  .services li:nth-child(3) { padding-left: 44px; }

  /* back */
  .back-scene { position: absolute; inset: 0; }
  .card--back .wordmark { right: 48px; top: 40px; text-align: left; }
  .contact-block { position: absolute; left: 40px; bottom: 24px; color: var(--white); }
  .person-name { font-weight: 700; font-size: 27px; line-height: 1.1; text-transform: uppercase; }
  .person-role { font-size: 18px; margin-bottom: 8px; }
  .contact-list { list-style: none; font-size: 17px; line-height: 27px; }
  .contact-list li { display: flex; align-items: center; gap: 9px; }
  .contact-list svg { width: 16px; height: 16px; flex: none; }
  .address { position: absolute; right: 40px; top: 262px; color: var(--white); font-size: 17px; line-height: 24px; text-align: right; font-style: normal; }
</style>
</head>
<body>

  <section class="card card--front" aria-label="Card front">
    <div class="front-scene" role="img" aria-label="Photo of a green crop field in Central Queensland under a pale blue sky"></div>
    <div class="drone-photo" role="img" aria-label="Photo of a Voskel Ferra Q80 agricultural spray drone with four sprayers, hovering above the field"></div>
    <h1 class="wordmark"><span>Larkmoor</span><span class="line-two">Drones</span></h1>
    <p class="region-band">Servicing Central Queensland</p>
    <ul class="services">
      <li>Spraying Weeds</li>
      <li>Spraying Crops</li>
      <li>Spreading Seeds</li>
    </ul>
  </section>

  <section class="card card--back" aria-label="Card back">
    <svg class="back-scene" viewBox="0 0 700 400" preserveAspectRatio="none" aria-hidden="true">
      <defs>
        <linearGradient id="field-tone" x1="0" y1="0" x2="0" y2="1">
          <stop offset="0" stop-color="#7f9b55"/>
          <stop offset=".45" stop-color="var(--field-mid)"/>
          <stop offset="1" stop-color="var(--field-dark)"/>
        </linearGradient>
      </defs>
      <path d="M0 185 C 80 145, 170 135, 260 165 C 350 195, 440 200, 540 190 C 620 183, 670 187, 700 190 L700 400 L0 400 Z" fill="var(--wave-pale)"/>
      <g role="img" aria-label="Photo of green crop rows stretching to a tree line in Central Queensland">
        <path d="M0 205 C 80 165, 170 155, 260 185 C 350 215, 440 220, 540 210 C 620 203, 670 207, 700 210 L700 400 L0 400 Z" fill="url(#field-tone)"/>
      </g>
    </svg>

    <h2 class="wordmark"><span>Larkmoor</span><span class="line-two">Drones</span></h2>

    <address class="address">17 Ridgeway Lane,<br>Dunmore Flats 4799<br>Australia</address>

    <div class="contact-block">
      <p class="person-name">Callum Reid</p>
      <p class="person-role">Managing Director</p>
      <ul class="contact-list">
        <li><svg viewBox="0 0 24 24" fill="none" stroke="#fff" stroke-width="2"><path d="M5 3h4l2 5-3 2a12 12 0 0 0 6 6l2-3 5 2v4a2 2 0 0 1-2 2A18 18 0 0 1 3 5a2 2 0 0 1 2-2z"/></svg>044-555 018 220</li>
        <li><svg viewBox="0 0 24 24" fill="none" stroke="#fff" stroke-width="2"><rect x="2" y="5" width="20" height="14" rx="1"/><path d="M2 6l10 7 10-7"/></svg>hello@larkmoordrones.example</li>
        <li><svg viewBox="0 0 24 24" fill="none" stroke="#fff" stroke-width="2"><circle cx="12" cy="12" r="10"/><path d="M2 12h20M12 2c3 3 4 6.5 4 10s-1 7-4 10c-3-3-4-6.5-4-10s1-7 4-10z"/></svg>www.larkmoordrones.example</li>
      </ul>
    </div>
  </section>

</body>
</html>
```